Non fiction book cover. The book advises how to get a new job.

The book size will be 20cm high by 13cm wide and I need a front cover which can wrap around to the back. This book has a serious message, but I've tried to make it quite light to read and accessible. So I don't want a cover that is too dour or serious and not frivolous either. At the end of the project, I will need a high resolution 3D image of the book, included as part of the package.<br/>The Title of the book is:- "Past Sixty? Hunting for your final post?<br/>by Gareth Millbrook-Ashdown".<br/>I am thinking of a light yellow background, with a striking image to attract attention. The image and words should be clear and sharp.<br/>Here is the, BACK COVER wording.<br/>"This book tells you clearly and simply the steps that you need to take, to get a job, once you’re over 50.<br/>It advises you on the techniques to use to write a killer CV.<br/>It explains how to ensure that your CV attention.<br/>It shows the best way to approach your local job agency.<br/>It demonstrates the best way to use your network.<br/><br/>This book, written by someone with 30 years’ experience in the recruitment industry, gives you ALL the answers.<br/>Whether you are a top executive or someone after some local part time work, then this book is for you. <br/>With the help of this book you will secure your next position.<br/>

Target Market(s)

UK, over 50s, male and female.

Font styles to use
Serif

Colors
fbee3e

Requirements
Must have
• A clear uncluttered cover.
Should not have
• Fussy and over complicated

```html
<!DOCTYPE html>
<html lang="en">
<head>
<meta charset="utf-8">
<title>Past Sixty? Hunting for your final post? — Book Cover Wrap</title>
<link rel="stylesheet" href="https://fonts.googleapis.com/css2?family=Bebas+Neue&family=Cinzel:wght@400;700&family=EB+Garamond:ital,wght@0,400;1,600&display=swap">
<style>
  :root {
    --cover-yellow: #fbee3e;
    --title-red: #d42f3c;
    --title-teal: #2aa596;
    --ink: #111111;
    --art-teal: #3dbfa5;
    --art-pink: #e5707a;
    --art-cyan: #00c9cc;
    --barcode-panel: #ffffff;
    --glow: rgba(255, 252, 215, 0.9);
  }
  * { margin: 0; padding: 0; box-sizing: border-box; }
  html, body { width: 1200px; height: 884px; overflow: hidden; background: var(--cover-yellow); }
  .cover-wrap { position: relative; width: 1200px; height: 884px; background: var(--cover-yellow); overflow: hidden; }

  /* Back cover */
  .back-cover { position: absolute; left: 0; top: 0; width: 567px; height: 884px; }
  .back-kicker {
    position: absolute; top: 44px; left: 0; width: 575px; text-align: center;
    font-family: "Cinzel", serif; font-weight: 400; font-size: 34px; line-height: 1; color: var(--title-teal);
  }
  .back-title {
    position: absolute; top: 86px; left: 0; width: 575px; text-align: center;
    font-family: "Bebas Neue", sans-serif; font-weight: 400; font-size: 52px; line-height: 1; color: var(--title-red);
    text-shadow: 0 0 10px var(--glow), 0 0 4px var(--glow);
  }
  .back-copy {
    position: absolute; left: 54px; top: 156px; width: 468px;
    font-family: "EB Garamond", serif; font-size: 17px; line-height: 22px; color: var(--ink);
    text-align: justify;
  }
  .selling-points {
    list-style: none; margin: 20px 0 34px 0;
    font-style: italic; font-weight: 600; font-size: 17.5px; text-align: left;
  }
  .selling-points li { position: relative; padding-left: 45px; margin-bottom: 15px; }
  .selling-points li::before {
    content: ""; position: absolute; left: 22px; top: 7px;
    width: 9px; height: 9px; border-radius: 50%; background: var(--ink);
  }
  .back-copy .closing { margin-top: 22px; }
  .back-artwork {
    position: absolute; left: 62px; top: 572px; width: 364px; height: 312px;
    background: linear-gradient(to bottom, rgba(0,201,204,.35) 0%, var(--art-pink) 50%, var(--art-teal) 100%);
  }
  .barcode-panel {
    position: absolute; left: 373px; top: 764px; width: 149px; height: 80px;
    background: var(--barcode-panel);
  }

  /* Spine */
  .spine {
    position: absolute; left: 567px; top: 0; width: 62px; height: 884px;
    display: flex; justify-content: center;
  }
  .spine-text {
    writing-mode: vertical-rl; padding-top: 52px;
    display: flex; align-items: center; white-space: nowrap;
  }
  .spine-kicker { font-family: "Cinzel", serif; font-size: 23px; color: var(--title-teal); }
  .spine-title {
    font-family: "Bebas Neue", sans-serif; font-size: 40px; color: var(--title-red); margin-top: 10px;
    text-shadow: 0 0 6px var(--glow);
  }
  .spine-author {
    font-family: "Cinzel", serif; font-weight: 700; font-size: 16px; color: var(--ink); margin-top: 20px;
  }

  /* Front cover */
  .front-cover { position: absolute; left: 629px; top: 0; width: 571px; height: 884px; }
  .front-author {
    position: absolute; top: 44px; left: 0; width: 571px; text-align: center;
    font-family: "Cinzel", serif; font-weight: 700; font-size: 28px; line-height: 1.1; color: var(--ink);
  }
  .front-kicker {
    position: absolute; top: 98px; left: 0; width: 571px; text-align: center;
    font-family: "Cinzel", serif; font-weight: 400; font-size: 60px; line-height: 1; color: var(--title-teal);
  }
  .front-title {
    position: absolute; top: 168px; left: 20px; width: 540px; text-align: center;
    font-family: "Bebas Neue", sans-serif; font-weight: 400; font-size: 110px; line-height: 92px; color: var(--title-red);
    text-shadow: 0 0 14px var(--glow), 0 0 5px var(--glow);
  }
  .front-artwork {
    position: absolute; left: 41px; top: 462px; width: 508px; height: 422px;
    background: linear-gradient(to bottom, rgba(0,201,204,.35) 0%, var(--art-pink) 50%, var(--art-teal) 100%);
  }
</style>
</head>
<body>
<main class="cover-wrap">
  <section class="back-cover">
    <div class="back-kicker">PAST SIXTY?</div>
    <h2 class="back-title">HUNTING FOR YOUR FINAL POST?</h2>
    <div class="back-copy">
      <p>This book tells you clearly and simply the steps that you need to take, to get a job, once you’re over 50.</p>
      <ul class="selling-points">
        <li>It advises you on the techniques to use to write a killer CV.</li>
        <li>It explains how to ensure that your CV gets attention.</li>
        <li>It shows the best way to approach your local job agency.</li>
        <li>It demonstrates the best way to use your network.</li>
      </ul>
      <p>This book, written by someone with 30 years’ experience in the recruitment industry, gives you ALL the answers. Whether you are a top executive or someone after some local part time work, then this book is for you.</p>
      <p class="closing">With the help of this book you will secure your next position.</p>
    </div>
    <div class="back-artwork" role="img" aria-label="Illustration: a traveller with a backpack resting on top of a faceted teal and pink mountain among clouds"></div>
    <div class="barcode-panel"></div>
  </section>

  <section class="spine">
    <div class="spine-text">
      <span class="spine-kicker">PAST SIXTY?</span>
      <span class="spine-title">HUNTING FOR YOUR FINAL POST?</span>
      <span class="spine-author">GARETH MILLBROOK-ASHDOWN</span>
    </div>
  </section>

  <section class="front-cover">
    <div class="front-author">GARETH MILLBROOK-ASHDOWN</div>
    <div class="front-kicker">PAST SIXTY?</div>
    <h1 class="front-title">HUNTING FOR<br>YOUR FINAL<br>POST?</h1>
    <div class="front-artwork" role="img" aria-label="Illustration: a traveller with a backpack sitting on the summit of a faceted teal and pink mountain with clouds around it"></div>
  </section>
</main>
</body>
</html>
```